Business Card Design for a Personal Trainer

I need a business card design for my job as a personal trainer. It should have a unique, modern and exclusive design. On the front there should be only my logo with my name and my job. 0162/3819204 Tobias Lendhart Wiesengrundweg 14 80417 Munich Germany The most important contact information is the web adress. it can be bigger than the rest, but its not necessary. The card should be 8,5cmx5,5cm big. Font: Roboto. Colors: black, white, gray, 56c1ff.

```html
<!DOCTYPE html>
<html lang="de">
<head>
<meta charset="utf-8">
<title>Tobias Lendhart – Visitenkarte</title>
<link href="https://fonts.googleapis.com/css2?family=Roboto:wght@400;500&display=swap" rel="stylesheet">
<style>
  :root {
    --stage: #5b5b5b;
    --card-white: #ffffff;
    --card-light: #f2f2f2;
    --band: #222222;
    --ink: #1a1a1a;
    --on-dark: #ffffff;
    --photo-top: #d6d6d6;
    --photo-bottom: #4a4a4a;
  }
  * { margin: 0; padding: 0; box-sizing: border-box; }
  html, body { width: 1200px; height: 802px; overflow: hidden; }
  body {
    background: var(--stage);
    font-family: "Roboto", sans-serif;
    position: relative;
  }
  .card {
    position: absolute;
    top: 274px;
    width: 442px;
    height: 265px;
    overflow: hidden;
    box-shadow: 2px 3px 6px rgba(0,0,0,0.45);
  }
  .card--contact { left: 136px; background: var(--card-white); }
  .card--brand { left: 624px; background: var(--card-light); }

  .band {
    position: absolute;
    left: 0; right: 0; bottom: 0;
    background: var(--band);
  }
  .card--contact .band { top: 130px; }
  .card--brand .band { top: 207px; }

  .portrait {
    position: absolute;
    left: 0; top: 20px;
    width: 172px; height: 245px;
    background: linear-gradient(180deg, var(--photo-top) 0%, #8a8a8a 45%, var(--photo-bottom) 100%);
  }

  .identity { position: absolute; text-align: center; color: var(--ink); }
  .identity__name {
    font-weight: 400;
    text-transform: uppercase;
    white-space: nowrap;
    line-height: 1;
  }
  .identity__role {
    display: flex;
    align-items: center;
    gap: 5px;
    text-transform: uppercase;
    letter-spacing: 0.22em;
    line-height: 1;
    white-space: nowrap;
  }
  .identity__role::before,
  .identity__role::after {
    content: "";
    flex: 1;
    height: 1px;
    background: var(--ink);
  }

  .card--contact .identity { left: 179px; width: 222px; top: 74px; }
  .card--contact .identity__name { font-size: 25px; }
  .card--contact .identity__role { font-size: 9px; margin-top: 4px; }

  .brand-mark {
    position: absolute;
    left: 191px; top: 50px;
    width: 60px; height: 60px;
    background: var(--ink);
  }

  .card--brand .identity { left: 84px; width: 274px; top: 134px; }
  .card--brand .identity__name { font-size: 31px; }
  .card--brand .identity__role { font-size: 11px; margin-top: 5px; }

  .contact-list {
    position: absolute;
    left: 227px; top: 143px;
    list-style: none;
    color: var(--on-dark);
    font-size: 14.5px;
    line-height: 18px;
  }
  .contact-list li { display: flex; align-items: center; gap: 6px; }
  .contact-list svg { width: 12px; height: 12px; fill: var(--on-dark); flex: none; }

  .address {
    position: absolute;
    left: 227px; top: 208px;
    color: var(--on-dark);
    font-size: 15px;
    line-height: 18px;
    font-style: normal;
  }

  .web {
    position: absolute;
    left: 0; right: 0; top: 224px;
    text-align: center;
    color: var(--on-dark);
    font-size: 16px;
  }
</style>
</head>
<body>

<section class="card card--contact">
  <div class="band"></div>
  <div class="portrait" role="img" aria-label="Schwarz-Weiß-Porträtfoto des Personal Trainers"></div>

  <div class="identity">
    <div class="identity__name">Tobias Lendhart</div>
    <div class="identity__role">Personal Trainer</div>
  </div>

  <ul class="contact-list">
    <li>
      <svg viewBox="0 0 12 12" aria-hidden="true"><path d="M1 4c0-1.5 2-2.5 5-2.5s5 1 5 2.5v1H8.5V4h-5v1H1z M2.5 6h7l1 4.5h-9z M6 7a1.2 1.2 0 1 0 0 2.4A1.2 1.2 0 0 0 6 7z"/></svg>
      0162/3819204
    </li>
    <li>
      <svg viewBox="0 0 12 12" aria-hidden="true"><path d="M0.5 2.5h11v7h-11z M1.5 3.3v0.4L6 6.8l4.5-3.1v-0.4z M1.5 4.8v3.9h9V4.8L6 7.9z" fill-rule="evenodd"/></svg>
      t.lendhart@postfeld.de
    </li>
    <li>
      <svg viewBox="0 0 12 12" aria-hidden="true"><circle cx="6" cy="6" r="5.5"/></svg>
      www.tobiaslendhart.de
    </li>
  </ul>

  <address class="address">
    Wiesengrundweg 14<br>
    80417 München
  </address>
</section>

<section class="card card--brand">
  <div class="band"></div>
  <div class="brand-mark" aria-hidden="true"></div>
  <div class="identity">
    <div class="identity__name">Tobias Lendhart</div>
    <div class="identity__role">Personal Trainer</div>
  </div>
  <div class="web">www.tobiaslendhart.de</div>
</section>

</body>
</html>
```